New website for concierge mobile medical service

new website for business:
WEBSITE REQUEST LIST:
Luxury product look.
Professional. Clean & simple, NO stock people photos. Graphics OK.
Black and white text.

```html
<!DOCTYPE html>
<html lang="en">
<head>
<meta charset="utf-8">
<title>Nimbus Health – Contact Us</title>
<link href="https://fonts.googleapis.com/css2?family=Lato:wght@400;700;900&display=swap" rel="stylesheet">
<style>
:root{
  --ink:#1a1a1a;
  --navy:#0f2a3a;
  --hero-dark:#02080d;
  --hero-blue:#07395a;
  --purple:#6a5fa8;
  --field-border:#dcdcdc;
  --button:#8bcfd8;
  --footer:#1f1f1f;
  --white:#ffffff;
  --ring-a:#5fe0f0;
  --ring-b:#6a5fc8;
}
*{margin:0;padding:0;box-sizing:border-box}
html,body{width:1200px;height:954px;overflow:hidden;background:var(--white)}
body{font-family:'Lato',sans-serif;color:var(--ink);position:relative}
.site-header{position:absolute;left:0;top:0;width:1200px;height:107px;background:var(--white);z-index:2}
.brand{position:absolute;left:156px;top:18px;width:124px;height:124px;border-radius:50%;background:var(--navy);border:6px solid var(--white);display:flex;align-items:center;justify-content:center;text-align:center;color:var(--white);font-weight:700;font-size:17px;line-height:1.1;z-index:3}
.phone{position:absolute;left:887px;top:16px;display:flex;align-items:center;gap:12px}
.phone-icon{width:32px;height:32px;background:var(--purple);border-radius:2px;display:flex;align-items:center;justify-content:center}
.phone-number{font-size:19.5px;font-weight:700;color:var(--purple);letter-spacing:.2px}
.main-nav{position:absolute;top:76px;left:0;width:1200px;height:31px}
.main-nav a{position:absolute;top:0;font-size:12.5px;font-weight:700;color:var(--ink);text-decoration:none;letter-spacing:.2px}
.main-nav a.active{color:var(--navy)}
.main-nav .underline{position:absolute;left:972px;top:25px;width:93px;height:6px;background:var(--navy)}
.hero{position:absolute;left:0;top:107px;width:1200px;height:264px;background:linear-gradient(90deg,var(--hero-dark) 0%,#041a2a 35%,var(--hero-blue) 70%,#073d60 100%)}
.hero-title{position:absolute;left:142px;top:104px;font-size:45px;font-weight:900;color:var(--white);line-height:1}
.hero-art{position:absolute;left:866px;top:31px;width:204px;height:204px;border-radius:50%;background:radial-gradient(circle,#0a4468 0%,#073a5c 70%,#3a6fb0 100%)}
.contact{position:absolute;left:0;top:371px;width:1200px;height:448px}
.contact h2{position:absolute;top:40px;width:100%;text-align:center;font-size:32px;font-weight:700}
.contact .intro{position:absolute;top:93px;width:100%;text-align:center;font-size:15.5px}
.field{position:absolute;border:2px solid var(--field-border);background:var(--white);font-size:12.5px;color:var(--ink);padding:0 15px;display:flex;align-items:center}
.field.message{align-items:flex-start;padding-top:20px}
.submit{position:absolute;left:277px;top:351px;width:648px;height:44px;background:var(--button);border-radius:2px;color:var(--white);font-size:16px;font-weight:700;display:flex;align-items:center;justify-content:center;letter-spacing:.3px}
.site-footer{position:absolute;left:0;top:819px;width:1200px;height:135px;background:var(--footer);color:var(--white)}
.footer-nav{position:absolute;top:24px;left:0;width:1200px;text-align:center;font-size:13px;font-weight:700}
.footer-nav span{margin:0 18px}
.copyright{position:absolute;top:59px;width:100%;text-align:center;font-size:11.5px}
.social{position:absolute;top:89px;left:0;width:1200px;display:flex;justify-content:center;gap:16px}
.social span{width:18px;height:18px;border-radius:50%;background:var(--white)}
</style>
</head>
<body>
<header class="site-header">
  <div class="brand">Nimbus<br>Health</div>
  <div class="phone">
    <div class="phone-icon">
      <svg width="16" height="16" viewBox="0 0 24 24"><path fill="#fff" d="M6.6 10.8a15.1 15.1 0 0 0 6.6 6.6l2.2-2.2c.3-.3.7-.4 1-.2 1.1.4 2.3.6 3.6.6.6 0 1 .4 1 1V20c0 .6-.4 1-1 1A17 17 0 0 1 3 4c0-.6.4-1 1-1h3.5c.6 0 1 .4 1 1 0 1.3.2 2.5.6 3.6.1.3 0 .7-.2 1z"/></svg>
    </div>
    <span class="phone-number">555-010-0199</span>
  </div>
  <nav class="main-nav">
    <a style="left:394px">HOME</a>
    <a style="left:474px">ABOUT US</a>
    <a style="left:579px">WHY NIMBUS?</a>
    <a style="left:695px">SERVICE AREA</a>
    <a style="left:826px">OTHER</a>
    <a style="left:910px">FAQ</a>
    <a class="active" style="left:974px">CONTACT US</a>
    <div class="underline"></div>
  </nav>
</header>

<section class="hero">
  <h1 class="hero-title">Contact Us</h1>
  <div class="hero-art" role="img" aria-label="Illustration of a medical vehicle with a caduceus inside a glowing ring"></div>
</section>

<main class="contact">
  <h2>Contact Us</h2>
  <p class="intro">We want to hear from you! Click below to send us a message and receive upcoming information.</p>
  <div class="field" style="left:224px;top:131px;width:365px;height:41px">Enter Name</div>
  <div class="field" style="left:613px;top:131px;width:366px;height:41px">Enter Email Address</div>
  <div class="field" style="left:224px;top:183px;width:365px;height:41px">Phone No</div>
  <div class="field" style="left:613px;top:183px;width:366px;height:41px">Subject</div>
  <div class="field message" style="left:224px;top:235px;width:755px;height:100px">Message</div>
  <div class="submit">SUBMIT NOW</div>
</main>

<footer class="site-footer">
  <div class="footer-nav"><span>HOME</span><span>ABOUT US</span><span>WHY NIMBUS?</span><span>SERVICE AREA</span><span>OTHER</span><span>CONTACT US</span></div>
  <p class="copyright">Copyright © 2019. Company Name All Rights Reserved</p>
  <div class="social" aria-label="Social links"><span></span><span></span><span></span><span></span><span></span></div>
</footer>
</body>
</html>
```